Business Card Update, need to bring life to the card, two sided color

We need a new business card design, are moving and changing addresses and need a new look, we have the logos already attached but need a new style moving forward. Can incorporate the color of the logo (The Green) as well, maybe a solid back? We deal with safety products revolving around static electricity and safety lighting. Would like to keep same font in second logo as well.

Target Market(s)

Electrical Safety, Lighting

Contact Information for Business Card

Dale Fenwick
Vice President
Office: 770-555-4821
Cell: 770-555-3067
dale@tkfenwick.example
www.tkfenwick.example
4700 West Harbor Boulevard
Suite #150
Roswell, GA 30076

Font styles to use
Serif
Sans Serif

Requirements
Must have
• Since 1918
Nice to have
• Could use the 100 Year Logo for back of card, would like the back of card to be the same green as logo.
Should not have
• No black cards please.

```html
<!DOCTYPE html>
<html lang="en">
<head>
<meta charset="utf-8">
<title>T.K. Fenwick Business Card</title>
<link rel="stylesheet" href="https://fonts.googleapis.com/css2?family=Montserrat:wght@300;600&family=Open+Sans:wght@400;600&display=swap">
<style>
  :root {
    --page-bg: #2a2a2a;
    --card-front-bg: #3c4442;
    --card-back-bg: #1ea85c;
    --card-edge: #222827;
    --brand-green: #2fc071;
    --text-white: #f4f4f4;
    --text-soft: #d3d9d6;
    --emboss-line: #4d5654;
    --emboss-shadow: #2e3533;
  }
  * { margin: 0; padding: 0; box-sizing: border-box; }
  html, body {
    width: 1200px; height: 672px; overflow: hidden;
    background: var(--page-bg);
  }
  .stage {
    position: relative; width: 1200px; height: 672px;
    display: flex; align-items: center; justify-content: center; gap: 40px;
  }
  .card {
    position: relative; width: 540px; height: 309px;
    border: 1px solid var(--card-edge);
    box-shadow: 0 10px 30px rgba(0,0,0,.45);
    overflow: hidden;
  }
  .card-front { background: var(--card-front-bg); }
  .card-back { background: var(--card-back-bg); }

  /* Front side */
  .identity { position: absolute; left: 40px; top: 34px; }
  .person-name {
    font-family: "Montserrat", sans-serif; font-size: 24px; letter-spacing: 1px;
    color: var(--text-white); font-weight: 300; text-transform: uppercase;
  }
  .person-name strong { font-weight: 600; }
  .job-title {
    margin-top: 4px; font-family: "Open Sans", sans-serif; font-size: 12px;
    letter-spacing: 1px; color: var(--brand-green); text-transform: uppercase;
  }
  .contact-list {
    position: absolute; left: 40px; bottom: 28px; list-style: none;
    font-family: "Open Sans", sans-serif; font-size: 12px; color: var(--text-white);
  }
  .contact-list li { display: flex; align-items: flex-start; gap: 10px; line-height: 20px; }
  .contact-icon { width: 11px; height: 11px; flex: none; margin-top: 4px; }
  .contact-label { color: var(--brand-green); font-weight: 600; margin-right: 4px; }
  .address-lines { color: var(--text-soft); }
  .emboss-mark {
    position: absolute; right: 48px; top: 50%; transform: translateY(-50%);
    display: flex; flex-direction: column; align-items: center; gap: 10px;
  }
  .emboss-circle {
    width: 96px; height: 96px; border-radius: 50%;
    border: 2px solid var(--emboss-line);
    box-shadow: 1px 1px 0 var(--emboss-shadow), inset 1px 1px 0 var(--emboss-shadow);
  }
  .emboss-name {
    font-family: "Open Sans", sans-serif; font-weight: 600; font-size: 13px;
    color: var(--emboss-line); text-shadow: 1px 1px 0 var(--emboss-shadow);
  }

  /* Back side */
  .brand-lockup {
    position: absolute; left: 48px; top: 50%; transform: translateY(-50%);
    display: flex; align-items: center; gap: 22px;
  }
  .brand-circle {
    width: 92px; height: 92px; border-radius: 50%; background: var(--text-white); flex: none;
  }
  .brand-name {
    font-family: "Open Sans", sans-serif; font-weight: 600; color: var(--text-white);
  }
  .brand-name .brand-primary { display: block; font-size: 30px; line-height: 1.1; }
  .brand-name .brand-secondary { display: block; font-size: 14px; margin-top: 4px; }
  .brand-name .brand-since {
    display: block; font-size: 12px; margin-top: 10px; letter-spacing: 2px; text-transform: uppercase;
  }
</style>
</head>
<body>
<main class="stage">
  <section class="card card-front" aria-label="Card front">
    <div class="identity">
      <h1 class="person-name">Dale <strong>Fenwick</strong></h1>
      <p class="job-title">Vice President</p>
    </div>
    <ul class="contact-list">
      <li>
        <svg class="contact-icon" viewBox="0 0 12 12" aria-hidden="true"><rect width="12" height="12" rx="2" fill="#2fc071"/><path d="M3.5 3h1.5l.7 1.7-.9.7a5 5 0 0 0 1.8 1.8l.7-.9L9 7v1.5c0 .4-.3.6-.7.6A5.8 5.8 0 0 1 2.9 3.7c0-.4.2-.7.6-.7z" fill="#3c4442"/></svg>
        <span><span class="contact-label">Office</span>770-555-4821 &nbsp; <span class="contact-label">Cell</span>770-555-3067</span>
      </li>
      <li>
        <svg class="contact-icon" viewBox="0 0 12 12" aria-hidden="true"><rect width="12" height="12" rx="2" fill="#2fc071"/><rect x="2.5" y="3.5" width="7" height="5" fill="none" stroke="#3c4442" stroke-width="1"/><path d="M2.5 3.5 6 6.5l3.5-3" fill="none" stroke="#3c4442" stroke-width="1"/></svg>
        <span>dale@tkfenwick.example</span>
      </li>
      <li>
        <svg class="contact-icon" viewBox="0 0 12 12" aria-hidden="true"><circle cx="6" cy="6" r="6" fill="#2fc071"/><path d="M1 6h10M6 1c-2 2.5-2 7.5 0 10M6 1c2 2.5 2 7.5 0 10" fill="none" stroke="#3c4442" stroke-width=".8"/></svg>
        <span>www.tkfenwick.example</span>
      </li>
      <li>
        <svg class="contact-icon" viewBox="0 0 12 12" aria-hidden="true"><path d="M6 0.5a4 4 0 0 1 4 4c0 3-4 7-4 7s-4-4-4-7a4 4 0 0 1 4-4z" fill="#2fc071"/><circle cx="6" cy="4.5" r="1.4" fill="#3c4442"/></svg>
        <span class="address-lines">4700 West Harbor Boulevard, Suite #150<br>Roswell, GA 30076</span>
      </li>
    </ul>
    <div class="emboss-mark">
      <span class="emboss-circle"></span>
      <span class="emboss-name">T.K. Fenwick</span>
    </div>
  </section>

  <section class="card card-back" aria-label="Card back">
    <div class="brand-lockup">
      <span class="brand-circle"></span>
      <p class="brand-name">
        <span class="brand-primary">T.K. Fenwick</span>
        <span class="brand-secondary">Manufacturing Company, Inc.</span>
        <span class="brand-since">Since 1918</span>
      </p>
    </div>
  </section>
</main>
</body>
</html>
```